Creative, fresh business card design for Ripplecraft Facades

We need a fresh, creative business card design for Ripplecraft Facades. We are the manufacturer of Ripplecraft Facades in Australia. Wall panels are 2400 x 1200mm panels made from MDF and feature 3D patterns on the face of the panel. The colours to be used are green, silver/grey and white RGB
Red 187
Green 207
Blue 65.

An idea is to possibly use a watermark of one of our designs as a background (like on the "Grids" design on the left hand side of page 2 of our brochure).

Target Market(s)

Interior designers, architects, builders and home renovators

Industry/Entity Type

Business

Contact Information for Business Card

Details to go on the card are:
Our logo (attached),
Slogan: "Decorative panels for interiors and exteriors",
Contact name,
Position,
Mobile phone number,
Business address,
Business phone,
Business fax,
Website and
Email address.

I have attached a few images of our panels and our brochure for reference.

The colours of the business card should feature our logo colours which are: RGB
Red 187
Green 207
Blue 65

Requirements
Must have
• Very modern fonts and design. Some of the designs shown especially the "Prisms" design which is a popular design.
Nice to have
• Creative but simple design. Very contemporary.
Should not have
• Anything ornate or old fashioned.

```html
<!DOCTYPE html>
<html lang="en">
<head>
<meta charset="utf-8">
<title>Ripplecraft Facades – Business Card</title>
<link href="https://fonts.googleapis.com/css2?family=Montserrat:wght@500;600;700&family=PT+Sans:wght@400;700&display=swap" rel="stylesheet">
<style>
  :root {
    --bg: #ececec;
    --card: #f7f7f7;
    --green: rgb(187, 207, 65);
    --grey: #8f9092;
    --ink: #2b2b2b;
    --pattern-a: #f2f2f2;
    --pattern-b: #e6e6e6;
  }
  * { box-sizing: border-box; margin: 0; padding: 0; }
  html, body {
    width: 1200px; height: 900px; overflow: hidden;
    background: var(--bg);
    font-family: "PT Sans", Arial, sans-serif;
  }
  .canvas {
    position: relative; width: 1200px; height: 900px;
  }
  .card {
    position: absolute;
    width: 525px; height: 300px;
    background: var(--card);
    box-shadow: 0 6px 18px rgba(0,0,0,.12);
    overflow: hidden;
  }
  .card--front { left: 50px; top: 300px; }
  .card--back  { left: 625px; top: 300px; }

  .panel-texture {
    position: absolute;
    background: linear-gradient(135deg, var(--pattern-a) 0%, var(--pattern-b) 55%, var(--card) 100%);
  }
  .card--front .panel-texture { left: 0; top: 0; width: 300px; height: 170px;
    -webkit-mask-image: linear-gradient(135deg, #000 40%, transparent 100%);
            mask-image: linear-gradient(135deg, #000 40%, transparent 100%); }
  .card--back .panel-texture { left: 0; top: 0; width: 320px; height: 300px;
    -webkit-mask-image: linear-gradient(90deg, #000 30%, transparent 100%);
            mask-image: linear-gradient(90deg, #000 30%, transparent 100%); }

  .holder { position: absolute; left: 34px; top: 30px; }
  .holder__name {
    font-family: "Montserrat", Arial, sans-serif;
    font-weight: 700; font-size: 15px; letter-spacing: .5px;
    color: var(--green); text-transform: uppercase;
  }
  .holder__role { font-size: 12px; color: var(--ink); margin-top: 2px; }

  .contact-list { position: absolute; left: 34px; top: 100px; list-style: none; }
  .contact-list li {
    display: flex; align-items: center; gap: 8px;
    font-size: 12.5px; color: var(--ink); line-height: 18px;
  }
  .contact-list svg { width: 10px; height: 10px; flex: none; }

  .wordmark {
    position: absolute; display: flex; align-items: center; gap: 10px;
    font-family: "Montserrat", Arial, sans-serif;
    font-weight: 600; color: var(--green);
  }
  .wordmark__square { background: var(--green); flex: none; }
  .card--front .wordmark { right: 36px; top: 135px; font-size: 22px; }
  .card--front .wordmark__square { width: 26px; height: 26px; }
  .card--back .wordmark { right: 46px; top: 110px; font-size: 28px; }
  .card--back .wordmark__square { width: 34px; height: 34px; }

  .address {
    position: absolute; right: 60px; top: 212px;
    font-size: 12.5px; line-height: 17px; color: var(--ink);
  }
  .slogan {
    position: absolute; right: 46px; top: 165px; width: 300px;
    font-family: "Montserrat", Arial, sans-serif;
    font-weight: 600; font-size: 13px; line-height: 17px; letter-spacing: .6px;
    color: var(--green); text-transform: uppercase;
  }
</style>
</head>
<body>
<main class="canvas">

  <section class="card card--front" aria-label="Business card front">
    <div class="panel-texture" role="img" aria-label="Faint embossed geometric wall-panel pattern"></div>

    <div class="holder">
      <p class="holder__name">Marcus Ellery</p>
      <p class="holder__role">Managing Director</p>
    </div>

    <ul class="contact-list">
      <li><svg viewBox="0 0 10 10"><path fill="rgb(187,207,65)" d="M2 0h2l1 2.5-1.3 1a5.5 5.5 0 0 0 2.8 2.8l1-1.3L10 6v2a2 2 0 0 1-2 2A8 8 0 0 1 0 2a2 2 0 0 1 2-2z"/></svg>044-555 010 222</li>
      <li><svg viewBox="0 0 10 10"><rect x="2" y="0" width="6" height="10" rx="1" fill="rgb(187,207,65)"/><rect x="3" y="1.5" width="4" height="6" fill="#f7f7f7"/></svg>044-555 010 333</li>
      <li><svg viewBox="0 0 10 10"><rect x="0" y="3" width="10" height="5" fill="rgb(187,207,65)"/><rect x="2" y="0" width="6" height="3" fill="rgb(187,207,65)"/><rect x="2" y="8" width="6" height="2" fill="rgb(187,207,65)"/></svg>044-555 010 444</li>
      <li><svg viewBox="0 0 10 10"><rect x="0" y="1.5" width="10" height="7" fill="rgb(187,207,65)"/><path d="M0 1.5 5 6l5-4.5" stroke="#f7f7f7" fill="none"/></svg>hello@ripplecraft.com</li>
      <li><svg viewBox="0 0 10 10"><circle cx="5" cy="5" r="5" fill="rgb(187,207,65)"/></svg>www.ripplecraftfacades.com</li>
    </ul>

    <div class="wordmark"><span class="wordmark__square"></span>Ripplecraft Facades</div>

    <p class="address">48 Mill Lane, Geelong VIC 3220,<br>Australia.</p>
  </section>

  <section class="card card--back" aria-label="Business card back">
    <div class="panel-texture" role="img" aria-label="Faint embossed geometric wall-panel pattern"></div>

    <div class="wordmark"><span class="wordmark__square"></span>Ripplecraft Facades</div>

    <p class="slogan">Decorative panels for<br>interiors and exteriors</p>
  </section>

</main>
</body>
</html>
```